BOLD & MINIMALIST DESIGN NEEDED

We want a very bold but minimalistic business card design that is impactful and utilizes both sides of the business card. Our current logo is included for your use.

We want bold fonts and good use of negative space. We don't want the logo to overpower the design.

Target Market(s)

Professionals who are building new commercial buildings.

Industry/Entity Type

Construction

Contact Information for Business Card

Name, Title, email, office phone, cell phone, website

Font styles to use
Serif
Sans Serif

Requirements
Must have
• Bold design!

```html
<!DOCTYPE html>
<html lang="en">
<head>
<meta charset="utf-8">
<title>Ridgeway Design + Build — Business Card</title>
<link rel="stylesheet" href="https://fonts.googleapis.com/css2?family=Montserrat:wght@400;500;700;800&display=swap">
<style>
  :root {
    --bg: #3a3a3a;
    --card-black: #050505;
    --band-black: #1b1b1b;
    --card-white: #ffffff;
    --ink: #111111;
    --green: #7cc242;
    --muted: #2a2a2a;
  }
  * { box-sizing: border-box; margin: 0; padding: 0; }
  html, body { width: 1200px; height: 875px; overflow: hidden; }
  body {
    background: var(--bg);
    font-family: "Montserrat", sans-serif;
    position: relative;
  }
  .card {
    position: absolute;
    left: 280px;
    width: 640px;
    height: 366px;
    border-radius: 22px;
    overflow: hidden;
    box-shadow: 0 18px 40px rgba(0,0,0,.45);
  }
  .card--front { top: 48px; background: var(--card-black); }
  .card--back { top: 461px; background: var(--card-white); }

  .front-brand {
    position: absolute; inset: 0;
    display: flex; align-items: center; justify-content: center; gap: 16px;
  }
  .brand-mark {
    width: 34px; height: 34px; background: var(--green);
  }
  .brand-name {
    font-weight: 800; font-size: 58px; letter-spacing: 1px;
    color: #ffffff; text-transform: uppercase;
  }

  .back-band { position: absolute; inset: 0; }

  .back-brand {
    position: absolute; left: 78px; top: 132px;
    display: flex; align-items: center; gap: 9px;
  }
  .back-brand .brand-mark { width: 18px; height: 18px; }
  .back-brand .brand-name { font-size: 30px; color: var(--ink); letter-spacing: .5px; }

  .divider {
    position: absolute; left: 308px; top: 90px;
    width: 2px; height: 118px; background: var(--green);
  }

  .contact { position: absolute; left: 328px; top: 78px; color: var(--ink); }
  .contact__name { font-weight: 800; font-size: 25px; line-height: 1.1; }
  .contact__title { font-weight: 500; font-size: 12.5px; margin: 3px 0 12px; color: var(--muted); }
  .contact__list { list-style: none; }
  .contact__item {
    display: flex; align-items: center; gap: 10px;
    font-size: 13.5px; font-weight: 500; line-height: 21px; color: var(--muted);
  }
  .contact__icon { width: 13px; height: 13px; flex: none; }
</style>
</head>
<body>

<section class="card card--front" aria-label="Card front">
  <div class="front-brand">
    <span class="brand-mark"></span>
    <span class="brand-name">Ridgeway</span>
  </div>
</section>

<section class="card card--back" aria-label="Card back">
  <svg class="back-band" width="640" height="366" viewBox="0 0 640 366">
    <path d="M0 366 L0 334 Q470 326 640 222 L640 366 Z" fill="var(--band-black)"/>
    <path d="M100 320 Q470 305 615 190" fill="none" stroke="var(--green)" stroke-width="3" stroke-linecap="round"/>
  </svg>

  <div class="back-brand">
    <span class="brand-mark"></span>
    <span class="brand-name">Ridgeway</span>
  </div>

  <div class="divider"></div>

  <div class="contact">
    <p class="contact__name">Daniel Rowe</p>
    <p class="contact__title">CEO &amp; Founder</p>
    <ul class="contact__list">
      <li class="contact__item">
        <svg class="contact__icon" viewBox="0 0 16 16"><path d="M3 1h3l1.5 4-2 1.3a8 8 0 0 0 4.2 4.2L11 8.5l4 1.5v3a2 2 0 0 1-2 2A12 12 0 0 1 1 3a2 2 0 0 1 2-2z" fill="var(--green)"/></svg>
        (555) 214-0386
      </li>
      <li class="contact__item">
        <svg class="contact__icon" viewBox="0 0 16 16"><rect x="4" y="1" width="8" height="14" rx="1.5" fill="var(--green)"/><rect x="5.5" y="3" width="5" height="8" fill="#fff"/></svg>
        1-800-555-0142
      </li>
      <li class="contact__item">
        <svg class="contact__icon" viewBox="0 0 16 16"><rect x="1" y="3" width="14" height="10" rx="1" fill="var(--green)"/><path d="M1.5 3.5 8 9l6.5-5.5" fill="none" stroke="#fff" stroke-width="1.4"/></svg>
        info@ridgewaybuild.com
      </li>
      <li class="contact__item">
        <svg class="contact__icon" viewBox="0 0 16 16"><circle cx="8" cy="8" r="7" fill="var(--green)"/><path d="M1 8h14M8 1c-3 3.5-3 10.5 0 14M8 1c3 3.5 3 10.5 0 14" fill="none" stroke="#fff" stroke-width="1"/></svg>
        www.ridgewaybuild.com
      </li>
    </ul>
  </div>
</section>

</body>
</html>
```